Business Card Design

Business Card for professional consulting firm working with large financial institutions.

Target Market(s)

Executive buyers

Industry/Entity Type

Banking

Contact Information for Business Card

Mild creativity wanted. Not boring, but do elaborate artwork.

Font styles to use
Serif
Sans Serif

Colors

Designer to choose colors to be used in the design.

Requirements
Must have
• Standard business card features - company name, individual name, telephone, website, email, locations.
Nice to have
• Two colors
Should not have
• too many colors, fancy printing, cartoons.

```html
<!DOCTYPE html>
<html lang="en">
<head>
<meta charset="utf-8">
<title>Northvale business card</title>
<link rel="stylesheet" href="https://fonts.googleapis.com/css2?family=Tinos:wght@400;700&display=swap">
<style>
  :root {
    --page: #e4e2df;
    --ink: #111111;
    --ink-soft: #2b2b2b;
    --paper: #ffffff;
    --paper-shade: #f1f1f1;
    --swoop: #c9c9c9;
    --muted: #9a9a9a;
    --text: #3a3a3a;
  }
  html, body {
    margin: 0;
    padding: 0;
    width: 1200px;
    height: 886px;
    overflow: hidden;
    background: var(--page);
  }
  .canvas {
    position: relative;
    width: 1200px;
    height: 886px;
    display: flex;
    align-items: center;
    justify-content: center;
    gap: 40px;
  }
  .card {
    position: relative;
    width: 540px;
    height: 310px;
    border-radius: 22px;
    overflow: hidden;
    box-shadow: 0 10px 28px rgba(0,0,0,0.25);
    font-family: "Tinos", "Times New Roman", serif;
  }
  .card-back {
    background: linear-gradient(100deg, var(--ink) 0%, var(--ink-soft) 45%, var(--ink) 100%);
    display: flex;
    align-items: center;
    justify-content: center;
  }
  .brand {
    display: flex;
    align-items: center;
    gap: 12px;
    font-size: 42px;
    font-weight: 400;
    letter-spacing: 1px;
    line-height: 1;
  }
  .card-back .brand { color: var(--paper); }
  .brand-mark {
    width: 12px;
    height: 12px;
    background: currentColor;
  }
  .card-front { background: var(--ink); }
  .card-front svg.shape {
    position: absolute;
    inset: 0;
  }
  .card-front .brand {
    position: absolute;
    top: 50px;
    right: 44px;
    font-size: 34px;
    color: var(--ink);
  }
  .contact {
    position: absolute;
    left: 34px;
    top: 118px;
    color: var(--text);
  }
  .person-name {
    margin: 0;
    font-size: 26px;
    font-weight: 700;
    color: var(--ink);
    line-height: 1.05;
  }
  .person-title {
    margin: 0 0 10px;
    font-size: 17px;
    color: var(--muted);
  }
  .address {
    margin: 0 0 6px;
    font-size: 15px;
    line-height: 1.2;
  }
  .lines { list-style: none; margin: 0; padding: 0; font-size: 15px; line-height: 1.35; }
  .lines li { display: flex; align-items: center; gap: 8px; }
  .lines svg { width: 12px; height: 12px; fill: var(--ink); flex: none; }
</style>
</head>
<body>
<main class="canvas">
  <section class="card card-back" aria-label="Card back">
    <div class="brand"><span class="brand-mark"></span><span>Northvale</span></div>
  </section>

  <section class="card card-front" aria-label="Card front">
    <svg class="shape" viewBox="0 0 540 310" preserveAspectRatio="none" aria-hidden="true">
      <path d="M0 120 C 60 30, 200 0, 330 0 L540 0 L540 310 L0 310 Z" fill="var(--paper)"/>
      <path d="M540 70 C 540 200, 420 290, 260 310 L540 310 Z" fill="var(--swoop)"/>
      <path d="M520 80 C 515 200, 400 280, 250 310 L260 310 C 420 290, 540 200, 540 70 Z" fill="var(--paper-shade)"/>
    </svg>
    <div class="brand"><span class="brand-mark"></span><span>Northvale</span></div>
    <div class="contact">
      <p class="person-name">Daniel Marsh</p>
      <p class="person-title">Managing Director</p>
      <p class="address">1420 Alder Court<br>Juneau, Alaska 99801</p>
      <ul class="lines">
        <li><svg viewBox="0 0 12 12"><path d="M2.5 1 L4.5 1 L5.3 3.5 L4 4.5 C4.7 6 6 7.3 7.5 8 L8.5 6.7 L11 7.5 L11 9.5 C11 10.3 10.3 11 9.5 11 C5 11 1 7 1 2.5 C1 1.7 1.7 1 2.5 1Z"/></svg>907 555 0142</li>
        <li><svg viewBox="0 0 12 12"><path d="M1 3 L11 3 L11 10 L1 10 Z M1.5 3.5 L6 7 L10.5 3.5" stroke="var(--paper)" stroke-width="0.8"/></svg>info@northvale.com</li>
        <li><svg viewBox="0 0 12 12"><circle cx="6" cy="6" r="5"/></svg>www.northvale.com</li>
      </ul>
    </div>
  </section>
</main>
</body>
</html>
```